Harborline Renewal Business Card Design

Professional and clean design. The design colors should flow with the logo. Two-sided card with the website on the back which is:

www.HarborlineRenewal.example.

"Specializing in Water Damage Restoration"

On the front I need the name, email, phone, and logo.

Name: Darnell Quisby
Email: Darnell@HarborlineRenewal.example
Phone: 555-318-2046 for now

I only have the Preview and Thumbnail right now but should have the source files uploaded within a day or two.

Target Market(s)

Flood victims, home owners with water damage from busted pipes etc...

Industry/Entity Type

Business

Contact Information for Business Card

Name: Darnell Quisby

Font styles to use
Serif
Sans Serif

Requirements
Must have
• Business Card Details Info

```html
<!DOCTYPE html>
<html lang="en">
<head>
<meta charset="utf-8">
<title>Harborline Renewal Business Card</title>
<link href="https://fonts.googleapis.com/css2?family=Cinzel:wght@500;600&family=Open+Sans:ital,wght@0,400;0,600;1,600&display=swap" rel="stylesheet">
<style>
  :root {
    --page: #e9ebee;
    --brand-blue: #2f98d6;
    --brand-blue-deep: #1d7fc0;
    --brand-blue-light: #49b0e6;
    --card-white: #ffffff;
    --card-grey: #e6e7e9;
    --swoosh-grey: #a9abae;
    --text-grey: #5a5c60;
  }
  * { margin: 0; padding: 0; box-sizing: border-box; }
  html, body { width: 1200px; height: 843px; overflow: hidden; }
  body {
    background: var(--page);
    position: relative;
    font-family: "Open Sans", Arial, sans-serif;
  }
  .card {
    position: absolute;
    left: 300px;
    width: 600px;
    height: 343px;
    border-radius: 18px;
    overflow: hidden;
    box-shadow: 0 8px 24px rgba(0,0,0,0.18);
  }
  .card-back { top: 50px; }
  .card-front { top: 443px; background: var(--card-white); }
  .card-art { position: absolute; inset: 0; width: 100%; height: 100%; }

  /* back side */
  .back-identity {
    position: absolute;
    left: 34px;
    bottom: 38px;
    z-index: 1;
  }
  .back-wordmark {
    font-family: "Cinzel", Georgia, serif;
    font-weight: 600;
    font-size: 30px;
    letter-spacing: 1px;
    color: var(--card-white);
    line-height: 1;
    margin-bottom: 14px;
  }
  .back-tagline {
    font-style: italic;
    font-weight: 600;
    font-size: 15px;
    color: var(--card-white);
  }

  /* front side */
  .front-logo {
    position: absolute;
    right: 36px;
    top: 74px;
    display: flex;
    flex-direction: column;
    align-items: center;
    gap: 10px;
  }
  .logo-dot {
    width: 46px;
    height: 46px;
    border-radius: 50%;
    background: var(--brand-blue);
  }
  .logo-name {
    font-family: "Cinzel", Georgia, serif;
    font-weight: 600;
    font-size: 25px;
    color: var(--brand-blue-deep);
    text-align: center;
    line-height: 1.15;
  }
  .contact-block {
    position: absolute;
    left: 40px;
    top: 112px;
  }
  .person-name {
    font-family: "Cinzel", Georgia, serif;
    font-weight: 500;
    font-size: 24px;
    color: var(--brand-blue);
    letter-spacing: 0.5px;
    margin-bottom: 12px;
  }
  .contact-list { list-style: none; }
  .contact-item {
    display: flex;
    align-items: center;
    gap: 12px;
    font-size: 15px;
    color: var(--text-grey);
    line-height: 27px;
  }
  .contact-icon { width: 14px; height: 14px; flex: none; }
</style>
</head>
<body>

  <section class="card card-back" aria-label="Card back">
    <svg class="card-art" viewBox="0 0 600 343" preserveAspectRatio="none" aria-hidden="true">
      <defs>
        <linearGradient id="backBlue" x1="0" y1="0" x2="1" y2="1">
          <stop offset="0" stop-color="#4fb3e8"/>
          <stop offset="1" stop-color="#1f84c6"/>
        </linearGradient>
      </defs>
      <rect width="600" height="343" fill="url(#backBlue)"/>
      <circle cx="480" cy="60" r="130" fill="none" stroke="#ffffff" stroke-width="16"/>
    </svg>
    <div class="back-identity">
      <div class="back-wordmark">HARBORLINE RENEWAL</div>
      <div class="back-tagline">Specializing in Water Damage Restoration</div>
    </div>
  </section>

  <section class="card card-front" aria-label="Card front">
    <svg class="card-art" viewBox="0 0 600 343" preserveAspectRatio="none" aria-hidden="true">
      <defs>
        <linearGradient id="frontWhite" x1="0" y1="0" x2="1" y2="1">
          <stop offset="0" stop-color="#ffffff"/>
          <stop offset="1" stop-color="#eceef0"/>
        </linearGradient>
      </defs>
      <rect width="600" height="343" fill="url(#frontWhite)"/>
      <path d="M0 0 L 230 0 C 130 8, 50 30, 0 70 Z" fill="var(--brand-blue)"/>
      <path d="M0 70 C 50 30, 130 8, 230 0 L 260 0 C 150 10, 60 40, 0 90 Z" fill="var(--card-grey)"/>
      <path d="M0 90 C 60 40, 150 10, 260 0 L 268 0 C 160 12, 70 44, 0 96 Z" fill="var(--swoosh-grey)"/>
      <path d="M600 230 C 570 290, 520 325, 440 343 L 600 343 Z" fill="var(--brand-blue)"/>
      <path d="M600 200 C 575 270, 520 315, 420 343 L 440 343 C 520 325, 570 290, 600 230 Z" fill="var(--swoosh-grey)"/>
    </svg>

    <div class="front-logo">
      <span class="logo-dot" aria-hidden="true"></span>
      <div class="logo-name">HARBORLINE<br>RENEWAL</div>
    </div>

    <div class="contact-block">
      <h1 class="person-name">DARNELL QUISBY</h1>
      <ul class="contact-list">
        <li class="contact-item">
          <svg class="contact-icon" viewBox="0 0 16 16" aria-hidden="true"><path d="M3 1 L6 1 L7 5 L5 6.5 C6 9 7 10 9.5 11 L11 9 L15 10 L15 13 C15 14 14 15 13 15 C6 15 1 10 1 3 C1 2 2 1 3 1 Z" fill="var(--brand-blue)"/></svg>
          <span>555-318-2046 for now</span>
        </li>
        <li class="contact-item">
          <svg class="contact-icon" viewBox="0 0 16 16" aria-hidden="true"><rect x="1" y="3" width="14" height="10" fill="var(--brand-blue)"/><path d="M1 3 L8 9 L15 3" fill="none" stroke="#ffffff" stroke-width="1.4"/></svg>
          <span>Darnell@HarborlineRenewal.example</span>
        </li>
        <li class="contact-item">
          <svg class="contact-icon" viewBox="0 0 16 16" aria-hidden="true"><circle cx="8" cy="8" r="7" fill="var(--brand-blue)"/><path d="M1 8 H15 M8 1 C5 4 5 12 8 15 C11 12 11 4 8 1" fill="none" stroke="#ffffff" stroke-width="1"/></svg>
          <span>www.HarborlineRenewal.example</span>
        </li>
      </ul>
    </div>
  </section>

</body>
</html>
```